Professional & attention grabbing.

A business card design, front and back. I already have a logo I will attach, but I am open to something new as well.
Things to include:
Name:
Title:
Phone:
Email:
Wanting something that is professional but attention grabbing.
Also we do a lot of work using drones on natural gas pipelines (leading the future)if you want to include any of that. I'm open to ideas.
Target Market(s)
Natural gas transmission industry / greenhouse gas mitigation industry
Industry/Entity Type
Business
Colors
Designer to choose colors to be used in the design.
Look and feel
Each slider illustrates characteristics of the customer's brand and the style your logo design should communicate.

```html
<!DOCTYPE html>
<html lang="en">
<head>
<meta charset="UTF-8">
<title>Business Card – Front and Back</title>
<link href="https://fonts.googleapis.com/css2?family=Open+Sans:wght@400;600;700&display=swap" rel="stylesheet">
<style>
  :root {
    --canvas: #ececec;
    --card: #f7f7f7;
    --orange: #e8750f;
    --grey: #6f6f6f;
    --ink: #2e2e2e;
    --sky-top: #e9c88f;
    --sky-mid: #c69a72;
    --ground: #5b4a52;
  }
  * { box-sizing: border-box; margin: 0; padding: 0; }
  html, body { width: 1200px; height: 900px; overflow: hidden; }
  body {
    background: var(--canvas);
    font-family: "Open Sans", Arial, sans-serif;
    display: flex;
    align-items: center;
    justify-content: center;
    gap: 60px;
  }
  .card {
    width: 525px;
    height: 300px;
    position: relative;
    box-shadow: 0 6px 18px rgba(0,0,0,0.12);
  }
  .card-front { background: var(--card); color: var(--ink); }
  .holder { position: absolute; left: 34px; top: 30px; }
  .holder-name { font-size: 17px; font-weight: 600; letter-spacing: 0.5px; color: var(--grey); }
  .holder-name .first { color: var(--orange); }
  .holder-title { font-size: 12px; color: var(--ink); margin-top: 1px; }
  .contact { position: absolute; left: 34px; top: 112px; list-style: none; font-size: 13px; line-height: 20px; }
  .contact li { display: flex; align-items: center; gap: 8px; }
  .contact svg { width: 11px; height: 11px; fill: var(--orange); }
  .brand {
    position: absolute; left: 270px; top: 120px;
    display: flex; align-items: center; gap: 10px;
    font-size: 21px; font-weight: 700; color: var(--grey); letter-spacing: 0.5px;
  }
  .brand-mark { width: 16px; height: 16px; background: var(--orange); }
  .address { position: absolute; left: 270px; top: 210px; font-size: 13px; line-height: 18px; }
  .card-back {
    background: linear-gradient(180deg, var(--sky-top) 0%, var(--sky-mid) 50%, var(--ground) 100%);
  }
  .website {
    position: absolute; left: 40px; bottom: 40px;
    color: #fff; font-size: 14px; letter-spacing: 0.3px;
  }
</style>
</head>
<body>
  <section class="card card-front" aria-label="Card front">
    <div class="holder">
      <p class="holder-name"><span class="first">MARCUS</span> ELLERY</p>
      <p class="holder-title">Managing Director</p>
    </div>
    <ul class="contact">
      <li>
        <svg viewBox="0 0 24 24" aria-hidden="true"><path d="M6.6 10.8a15 15 0 0 0 6.6 6.6l2.2-2.2a1 1 0 0 1 1-.25 11.4 11.4 0 0 0 3.6.6 1 1 0 0 1 1 1V20a1 1 0 0 1-1 1A17 17 0 0 1 3 4a1 1 0 0 1 1-1h3.5a1 1 0 0 1 1 1 11.4 11.4 0 0 0 .6 3.6 1 1 0 0 1-.25 1z"/></svg>
        (055)987654321
      </li>
      <li>
        <svg viewBox="0 0 24 24" aria-hidden="true"><path d="M2 5h20v14H2z M2 5l10 8 10-8" /></svg>
        hello@veltramail.com
      </li>
    </ul>
    <div class="brand">
      <span class="brand-mark" aria-hidden="true"></span>
      <span>Veltra Line Survey</span>
    </div>
    <p class="address">12345, Address Goes Here<br>Country Name, 123456.</p>
  </section>

  <section class="card card-back" role="img" aria-label="Photo of an inspection drone flying over a gas pipeline and refinery at sunset">
    <p class="website">www.veltraline.com</p>
  </section>
</body>
</html>
```